Healthcare and Professional IT Services Company need a redesigned business card

We are a IT Services company that targets small medical practices and professional business such as Attorneys, Accounts, Architects etc. We want to communicate a professional yet friendly image using recent logo redesign here on ArtHarbor. Like to see the colors blue and orange in the design. Must use the Tall Pine Computing as displayed in the new logo - then also want to incorporate the fish logo as well.

Target Market(s)

Small medical and professional services

Industry/Entity Type

It Company

Contact Information for Business Card

The usual stuff, place for name address phone website. Also maybe our tagline which is "rooted in technology"

Requirements
Must have
• My new logo and the fish somewhere on the card

```html
<!DOCTYPE html>
<html lang="en">
<head>
<meta charset="utf-8">
<title>Tall Pine Computing – Business Card</title>
<link href="https://fonts.googleapis.com/css2?family=Arimo:wght@400;700&display=swap" rel="stylesheet">
<style>
  :root {
    --blue: #1a8fd0;
    --blue-deep: #0a6fb0;
    --orange: #f39a1e;
    --ink: #555a5f;
    --paper: #ffffff;
    --silver-light: #f4f4f4;
    --silver-dark: #cfd0d2;
    --backdrop: #2a2b2d;
  }
  * { box-sizing: border-box; margin: 0; padding: 0; }
  html, body { width: 1200px; height: 871px; overflow: hidden; }
  body {
    background: var(--backdrop);
    font-family: "Arimo", Arial, sans-serif;
    display: flex;
    align-items: center;
    justify-content: center;
    gap: 40px;
  }
  .card {
    position: relative;
    width: 540px;
    height: 309px;
    overflow: hidden;
    box-shadow: 0 12px 30px rgba(0,0,0,.45);
  }
  .card--back {
    background: linear-gradient(135deg, var(--silver-light), var(--silver-dark));
    display: flex;
    flex-direction: column;
    align-items: center;
    justify-content: center;
  }
  .card--front { background: var(--paper); }

  .mascot {
    border-radius: 50% 45% 40% 50%;
    background: radial-gradient(ellipse at center, #d6ecf8, #a9d4ef);
  }
  .card--back .mascot { width: 150px; height: 68px; }
  .card--front .mascot { position: absolute; left: 72px; top: 26px; width: 130px; height: 62px; }

  .brand-name {
    font-weight: 700;
    color: var(--blue);
    letter-spacing: -0.5px;
  }
  .card--back .brand-name { font-size: 28px; margin-top: 12px; }
  .card--front .brand-name { position: absolute; left: 30px; top: 100px; font-size: 25px; }

  .tagline {
    margin-top: 12px;
    font-size: 14px;
    font-weight: 700;
    color: var(--blue-deep);
  }

  .divider {
    position: absolute;
    left: 30px; right: 36px; top: 170px;
    height: 1px;
    background: var(--blue);
  }
  .address {
    position: absolute;
    left: 30px; top: 180px;
    font-style: normal;
    font-size: 12.5px;
    line-height: 18px;
    color: var(--ink);
  }
  .holder {
    position: absolute;
    right: 36px; top: 132px;
    text-align: right;
  }
  .holder__name { font-size: 17px; font-weight: 700; color: var(--blue); }
  .holder__role { font-size: 13px; color: var(--orange); margin-top: 2px; }
  .contact {
    position: absolute;
    right: 36px; top: 180px;
    list-style: none;
    text-align: right;
    font-size: 12.5px;
    line-height: 18px;
    color: var(--ink);
  }
  .contact__label { color: var(--blue); }
  .wave { position: absolute; left: 0; bottom: 0; width: 540px; height: 120px; }
  .wave__band { fill: var(--blue); }
  .wave__line { fill: none; stroke: var(--orange); stroke-width: 5; }
</style>
</head>
<body>
  <section class="card card--back" aria-label="Card back">
    <div class="mascot" role="img" aria-label="Cartoon fish mascot"></div>
    <div class="brand-name">Tall Pine Computing</div>
    <div class="tagline">rooted in technology</div>
  </section>

  <section class="card card--front" aria-label="Card front">
    <div class="mascot" role="img" aria-label="Cartoon fish mascot"></div>
    <div class="brand-name">Tall Pine Computing</div>
    <div class="divider"></div>

    <address class="address">
      2710 Harbor Lane<br>
      Maple Falls, NY 10990
    </address>

    <div class="holder">
      <div class="holder__name">Jane Arden</div>
      <div class="holder__role">President</div>
    </div>

    <ul class="contact">
      <li><span class="contact__label">P :</span> 555 0142 3870</li>
      <li><span class="contact__label">E :</span> jane@tallpine.example</li>
      <li><span class="contact__label">W :</span> www.tallpine.example</li>
    </ul>

    <svg class="wave" viewBox="0 0 540 120" aria-hidden="true">
      <path class="wave__band" d="M0 58 C 60 90, 200 88, 330 94 C 430 100, 500 106, 540 120 L0 120 Z"/>
      <path class="wave__line" d="M0 40 C 60 78, 200 78, 330 85 C 430 91, 500 100, 540 116"/>
    </svg>
  </section>
</body>
</html>
```